Summer Sunglass offer

Need a poster design for a spring / summer campaign. We are an opticians with good footfall. The design needs to be eye catching and aimed at 40 year old plus. The offer is Up to 50% off sunglass offer, t&c apply. (I have attached our last year campaign)
Also need a 2 sided A5 leaflet design (see attached)
I've uploaded a copy of our logo

A5 leaflet should read:

Grab a bargain on two great looks this summer Upto 50% off sunglasses
Look great and stay safe in the sun this summer

We want you to look great, feel fantastic and most of all stay safe in the sun this summer. That’s why we’re offering you 50% off prescription sunglasses with every complete pair of glasses you buy this summer or 25% off for prescription sunglasses with no other purchase.
Find you new summer looks from our gorgeous collection of frames in store. It matters to us that you look great in your new glasses as much as how well you see through them, so we’ll be on hand to help you find frames that suit you best.
What new looks will you go for? Smart or sassy? Formal or Fun? Whatever you’re in the mood for, you’ll find it in our collections this summer.
Call in today to find your new looks, and remember to bring your prescription if you don’t need an eye test.

Target Market(s)

40 + year old

Industry/Entity Type

Optician

Colors

Designer to choose colors to be used in the design.

Requirements
Must have
• Images, preferably a male and Female image

```html
<!DOCTYPE html>
<html lang="en">
<head>
<meta charset="utf-8">
<title>Summer Sunglasses Offer Poster</title>
<link rel="stylesheet" href="https://fonts.googleapis.com/css2?family=Oswald:wght@300;500;600&family=Poppins:wght@400;500&display=swap">
<style>
  :root {
    --page-bg: #e4e7ea;
    --paper: #ffffff;
    --royal: #2a4ea3;
    --teal: #3aa6a8;
    --teal-light: #7fcfcc;
    --grey-title: #b9bcbf;
    --footer-grey: #a9abae;
    --ink: #3a3d42;
    --photo-a: #eef1f1;
    --photo-b: #d8c2a8;
    --photo-c: #c9dadb;
  }
  * { margin: 0; padding: 0; box-sizing: border-box; }
  html, body { width: 1200px; height: 805px; overflow: hidden; }
  body { background: var(--page-bg); position: relative; }

  .poster {
    position: absolute;
    left: 350px; top: 25px;
    width: 623px; height: 940px;
    transform: scale(0.8026);
    transform-origin: 0 0;
    background: var(--paper);
    overflow: hidden;
    box-shadow: 0 4px 14px rgba(0,0,0,0.18);
  }
  .poster-shapes { position: absolute; inset: 0; }

  .headline { position: absolute; right: 30px; top: 62px; text-align: right; }
  .headline-lead {
    font-family: 'Oswald', sans-serif; font-weight: 300;
    font-size: 40px; line-height: 1; color: var(--teal); letter-spacing: 0.5px;
  }
  .headline-main {
    font-family: 'Oswald', sans-serif; font-weight: 600;
    font-size: 92px; line-height: 1; color: var(--grey-title); margin-top: 4px;
  }

  .offer { position: absolute; left: 0; top: 530px; width: 320px; height: 160px; }
  .offer-upto {
    position: absolute; left: 18px; top: 108px;
    font-family: 'Oswald', sans-serif; font-weight: 600; font-size: 30px;
    color: var(--paper); transform: rotate(-90deg); transform-origin: 0 0; line-height: 1;
  }
  .offer-figure {
    position: absolute; left: 52px; top: 2px;
    font-family: 'Oswald', sans-serif; font-weight: 600; font-size: 116px;
    line-height: 1; color: var(--paper); letter-spacing: -2px;
  }
  .offer-percent {
    position: absolute; left: 172px; top: 6px;
    font-family: 'Oswald', sans-serif; font-weight: 300; font-size: 52px;
    line-height: 1; color: var(--royal);
  }
  .offer-off {
    position: absolute; left: 172px; top: 56px;
    font-family: 'Oswald', sans-serif; font-weight: 300; font-size: 50px;
    line-height: 1; color: var(--royal);
  }
  .offer-off sup { font-size: 26px; vertical-align: 22px; margin-left: 4px; }
  .offer-rule {
    position: absolute; left: 135px; top: 643px; width: 162px; height: 1.5px;
    background: var(--teal);
  }
  .offer-product {
    position: absolute; left: 135px; top: 650px;
    font-family: 'Oswald', sans-serif; font-size: 28px; line-height: 1.1; color: var(--teal);
  }
  .offer-product .light { font-weight: 300; }
  .offer-product .bold { font-weight: 600; }

  .tagline {
    position: absolute; right: 28px; top: 724px;
    font-family: 'Poppins', sans-serif; font-size: 15.5px; color: var(--royal);
  }

  .brand { position: absolute; right: 28px; top: 768px; display: flex; align-items: center; gap: 14px; }
  .brand-dot { width: 44px; height: 44px; border-radius: 50%; background: var(--teal); }
  .brand-name {
    font-family: 'Poppins', sans-serif; font-weight: 500; font-size: 27px;
    color: var(--royal); letter-spacing: 1px; line-height: 1;
  }

  .web-address {
    position: absolute; right: 30px; top: 835px;
    font-family: 'Poppins', sans-serif; font-size: 16px; color: var(--paper);
  }

  .terms {
    position: absolute; left: 0; right: 0; top: 888px;
    font-family: 'Poppins', sans-serif; font-size: 8.5px; line-height: 1.6;
    color: var(--ink); text-align: center;
  }
</style>
</head>
<body>
  <main class="poster">
    <svg class="poster-shapes" viewBox="0 0 623 940" width="623" height="940">
      <defs>
        <linearGradient id="photoTone" x1="0" y1="0" x2="1" y2="1">
          <stop offset="0" stop-color="var(--photo-a)"/>
          <stop offset="0.45" stop-color="var(--photo-b)"/>
          <stop offset="1" stop-color="var(--photo-c)"/>
        </linearGradient>
      </defs>
      <polygon class="hero-photo" role="img"
        aria-label="Photo of a woman with long wavy hair wearing dark sunglasses, hand resting on her cheek"
        points="85,0 623,0 623,505 445,630 85,430" fill="url(#photoTone)"/>
      <polygon class="chevron-band" points="0,360 445,612 623,490 623,520 445,645 0,395" fill="var(--teal-light)" opacity="0.45"/>
      <polygon class="chevron-band" points="0,380 445,628 623,505 623,535 445,660 0,415" fill="var(--teal)" opacity="0.45"/>
      <polygon class="chevron-band" points="0,395 445,640 623,520 623,545 445,668 0,430" fill="var(--teal)" opacity="0.7"/>
      <polygon class="offer-panel" points="0,430 255,570 0,705" fill="var(--royal)"/>
      <polygon class="web-bar-accent" points="330,860 360,828 380,828 350,860" fill="var(--teal-light)" opacity="0.7"/>
      <polygon class="web-bar-accent" points="355,860 385,828 405,828 375,860" fill="var(--teal)" opacity="0.7"/>
      <polygon class="web-bar" points="375,860 405,828 623,828 623,860" fill="var(--royal)"/>
      <rect class="terms-band" x="0" y="878" width="623" height="62" fill="var(--footer-grey)"/>
    </svg>

    <header class="headline">
      <p class="headline-lead">GET READY FOR</p>
      <h1 class="headline-main">SUMMER</h1>
    </header>

    <section class="offer">
      <span class="offer-upto">UP TO</span>
      <span class="offer-figure">50</span>
      <span class="offer-percent">%</span>
      <span class="offer-off">OFF<sup>*</sup></span>
    </section>
    <div class="offer-rule"></div>
    <p class="offer-product"><span class="light">FOR </span><span class="bold">SUNGLASSES</span></p>

    <p class="tagline">Look great and stay safe in the sun this season</p>

    <div class="brand">
      <span class="brand-dot"></span>
      <span class="brand-name">BEXLEY VISION STUDIO</span>
    </div>

    <p class="web-address">bexleyvisionstudio.co.uk</p>

    <p class="terms">*Offer includes frame from selected range, standard single vision lenses, tint and UV protection.<br>Lens upgrades available at extra cost. Offer excludes Coastline frames. Cannot be used with any other offer.</p>
  </main>
</body>
</html>
```